RW Framewell Inc Business cards

We need business cards using our existing logo but slightly modified. Right now the logo says RW Loadbearing Masonry. We want to keep the RW part of the design, but replace the Structural Concrete portion with "FRAMEWELL". Please see the attached file.
Ideally this would be a blank template so we can add Different Names, titles, and phone numbers later.
On the one side we want only the logo and on the other side the detail. I'm attaching an example for you to see.
Please reach out with any other questions. Our address and other details will be given out once we find a design we like.

Target Market(s)

Construction Industry

```html
<!DOCTYPE html>
<html lang="en">
<head>
<meta charset="UTF-8">
<title>RW Framewell Inc — Business Cards</title>
<link rel="stylesheet" href="https://fonts.googleapis.com/css2?family=Montserrat:wght@400;500;600;700&display=swap">
<style>
  :root {
    --backdrop: #2a7fe8;
    --card-grey: #e7eeef;
    --card-white: #ffffff;
    --brand-blue: #1f72be;
    --brand-grey: #8c8c8c;
    --ink: #1a1a1a;
    --ink-soft: #3a3a3a;
    --rule: #6f7477;
  }
  * { box-sizing: border-box; margin: 0; padding: 0; }
  html, body {
    width: 1200px; height: 900px; overflow: hidden;
    background: var(--backdrop);
    font-family: "Montserrat", sans-serif;
  }
  .canvas {
    position: relative; width: 1200px; height: 900px;
  }
  .card {
    position: absolute; left: 300px;
    width: 600px; height: 343px;
    background: var(--card-grey);
    overflow: hidden;
  }
  .card--details { top: 70px; }
  .card--logo { top: 487px; display: flex; align-items: center; justify-content: center; }

  .details__band {
    position: absolute; left: 0; top: 0; width: 100%; height: 82px;
    background: var(--card-white);
  }
  .wordmark {
    display: flex; align-items: center; gap: 10px;
    color: var(--brand-blue); font-weight: 700;
    letter-spacing: 0.12em; white-space: nowrap;
  }
  .wordmark__square { width: 14px; height: 14px; background: var(--brand-grey); }
  .wordmark--small { position: absolute; right: 40px; top: 70px; font-size: 18px; }
  .wordmark--small .wordmark__square { width: 10px; height: 10px; }
  .wordmark--large { font-size: 38px; }

  .person { position: absolute; left: 58px; top: 112px; }
  .person__name { font-size: 24px; font-weight: 700; color: var(--ink); letter-spacing: 0.01em; }
  .person__title {
    margin-top: 4px; font-size: 8.5px; font-weight: 500;
    letter-spacing: 0.16em; text-transform: uppercase; color: var(--ink-soft);
  }
  .contact { position: absolute; left: 58px; top: 174px; font-size: 10px; line-height: 1.5; color: var(--ink-soft); }
  .contact__heading { font-weight: 700; color: var(--ink); }
  .contact__row { display: flex; }
  .contact__label { width: 46px; }
  .contact__address { margin-top: 8px; }

  .details__rule { position: absolute; left: 0; top: 268px; width: 600px; height: 24px; }
  .site-pill {
    position: absolute; left: 350px; top: 268px; width: 130px; height: 24px;
    border: 1px solid var(--rule); border-radius: 12px;
    display: flex; align-items: center; justify-content: center;
    font-size: 8.5px; letter-spacing: 0.16em; color: var(--ink-soft);
  }
</style>
</head>
<body>
<main class="canvas">

  <section class="card card--details" aria-label="Business card, details side">
    <div class="details__band"></div>
    <div class="wordmark wordmark--small"><span class="wordmark__square"></span>RW FRAMEWELL</div>

    <div class="person">
      <p class="person__name">Daniel Hartwell</p>
      <p class="person__title">Chief Executive Officer / Owner</p>
    </div>

    <div class="contact">
      <p class="contact__heading">Contact Informations</p>
      <p class="contact__row"><span class="contact__label">Phone :</span>+00 (321) 7654 098</p>
      <p class="contact__row"><span class="contact__label">E-Mail :</span>founder@framewell.com</p>
      <p class="contact__address">42 Granite Avenue, 3rd Building<br>Boulder, CO - 80302</p>
    </div>

    <svg class="details__rule" viewBox="0 0 600 24" aria-hidden="true">
      <line x1="0" y1="12" x2="342" y2="12" stroke="#6f7477" stroke-width="1"/>
      <line x1="500" y1="12" x2="580" y2="12" stroke="#6f7477" stroke-width="1"/>
    </svg>
    <div class="site-pill">WWW.FRAMEWELL.COM</div>
  </section>

  <section class="card card--logo" aria-label="Business card, logo side">
    <div class="wordmark wordmark--large"><span class="wordmark__square"></span>RW FRAMEWELL</div>
  </section>

</main>
</body>
</html>
```